Shopify landing page redesign for the Tidewell Pillow

I am looking for someone with Shopify experience who can redesign our desktop and mobile landing page for the Tidewell Pillow. I am attaching my vision of what I think would convince visitors to purchase. The design should be highly focused on features and benefits and it needs to show how it solves our customer’s sleeping problems. It should also be designed with minimal distractions. Blue color is RGB: 0, 176, 24 or HEX: #00B0F0 I am looking for fast delivery.

```html
<!DOCTYPE html>
<html lang="en">
<head>
<meta charset="UTF-8">
<title>Tidewell Pillow – Adjust It. Fluff It. Love It.</title>
<link href="https://fonts.googleapis.com/css2?family=Poppins:wght@400;500;600;700;800&family=Red+Hat+Text:wght@400;500;700&display=swap" rel="stylesheet">
<style>
:root{
  --blue:#1f8fe6;
  --blue-dark:#1478c8;
  --blue-soft:#e6f2fc;
  --orange:#f47b20;
  --ink:#1c2330;
  --muted:#5b6472;
  --white:#ffffff;
  --line:#d7e3ef;
  --footer:#0b0b0d;
  --star:#ffc21a;
}
*{box-sizing:border-box;margin:0;padding:0}
html,body{width:1200px;height:3972px;overflow:hidden}
body{font-family:"Red Hat Text",Arial,sans-serif;color:var(--ink);background:var(--white);position:relative}
h1,h2,h3,.btn,.brand{font-family:"Poppins",Arial,sans-serif}
.btn{display:inline-block;background:var(--orange);color:var(--white);font-weight:600;font-size:17px;padding:14px 26px;border-radius:4px;text-transform:uppercase;letter-spacing:.3px}
.btn-blue{background:var(--blue)}

/* hero */
.hero{position:absolute;top:0;left:0;width:1200px;height:640px;background:var(--white);overflow:hidden}
.hero-bg{position:absolute;inset:0}
.brand{position:absolute;left:60px;top:34px;display:flex;align-items:center;gap:10px;color:var(--white);font-weight:700;font-size:24px}
.brand-dot{width:34px;height:34px;border-radius:50%;background:var(--white);opacity:.9}
.hero-buy{position:absolute;left:880px;top:26px;padding:12px 30px;font-size:17px}
.hero-copy{position:absolute;left:108px;top:210px;width:420px;color:var(--white)}
.stars{color:var(--star);font-size:22px;letter-spacing:3px}
.quote{font-family:"Poppins",sans-serif;font-weight:600;font-size:17px;margin-top:8px}
.hero h1{font-size:54px;line-height:1.05;font-weight:800;margin-top:12px;letter-spacing:.5px}
.hero p{font-size:17px;line-height:1.45;margin-top:16px;opacity:.95}
.hero .btn{margin-top:22px}
.guarantee{font-weight:700;font-size:17px;margin-top:18px}
.hero-photo{position:absolute;left:690px;top:90px;width:420px;height:520px;border-radius:210px 210px 40px 40px;background:linear-gradient(160deg,#e9f3fb,#c8ddef 60%,#a9c5dc)}

/* perks */
.perks{position:absolute;top:640px;left:0;width:1200px;height:340px}
.perk{position:absolute;top:120px;width:240px;text-align:center;font-weight:600;font-size:18px;font-family:"Poppins",sans-serif}
.perk-ring{width:96px;height:96px;margin:0 auto 22px;border-radius:50%;border:6px solid #cfe6f9;background:var(--blue);display:flex;align-items:center;justify-content:center}

/* pillows */
.pillows{position:absolute;top:980px;left:0;width:1200px;height:660px;background:var(--blue-soft)}
.section-title{text-align:center;font-weight:700;color:var(--blue);font-size:36px}
.pillows .section-title{margin-top:70px}
.pillow-card{position:absolute;top:160px;width:300px;height:400px;background:var(--white);box-shadow:0 4px 14px rgba(20,60,100,.12);text-align:center;padding:20px 22px}
.pillow-img{width:150px;height:150px;margin:0 auto;border-radius:50%;border:2px solid var(--line);background:radial-gradient(circle,#ffffff 30%,#dde9f4)}
.pillow-card h3{font-size:18px;font-weight:600;margin-top:22px}
.pillow-card p{font-size:15px;line-height:1.5;color:var(--muted);margin-top:12px}
.arrow{position:absolute;width:40px;height:40px;border-radius:50%;background:var(--white);border:1px solid #b8c6d4;display:flex;align-items:center;justify-content:center}

/* positions */
.positions{position:absolute;top:1640px;left:0;width:1200px;height:720px}
.positions .kicker{text-align:center;margin-top:96px;font-size:20px;font-family:"Poppins",sans-serif}
.positions .section-title{font-size:38px;margin-top:0}
.pos-card{position:absolute;width:230px;height:170px;background:var(--white);box-shadow:0 4px 16px rgba(20,40,70,.15);text-align:center;padding-top:82px;font-size:17px;line-height:1.45}
.pos-icon{position:absolute;left:75px;top:-30px;width:80px;height:80px;border-radius:50%;border:5px solid #d4e8f8;display:flex;align-items:center;justify-content:center}
.pos-icon.b{background:var(--blue)}
.pos-icon.o{background:var(--orange);border-color:#fde0c8}

/* reviews */
.reviews{position:absolute;top:2380px;left:0;width:1200px;height:560px;background:linear-gradient(180deg,#2a8fe0,#1c7fd2)}
.reviews .section-title{color:var(--white);margin-top:74px;font-size:34px}
.review{position:absolute;top:140px;width:300px;height:340px;border:2px solid rgba(255,255,255,.85);border-radius:8px;background:rgba(255,255,255,.06);padding:24px 22px;color:var(--white)}
.review .stars{font-size:18px}
.review p{font-size:14px;line-height:1.5;margin-top:12px}
.review hr{border:0;border-top:1px solid rgba(255,255,255,.6);margin:24px 0 18px}
.reviewer{display:flex;align-items:center;gap:14px}
.avatar{width:54px;height:54px;border-radius:50%;background:#f2d8c6;border:2px solid var(--white)}
.reviewer b{display:block;font-size:16px}
.reviewer span{font-size:14px;opacity:.9}

/* offers */
.offers{position:absolute;top:2940px;left:0;width:1200px;height:580px}
.offer-back{position:absolute;left:140px;top:130px;width:290px;height:340px;background:#dcebf8}
.offer-photo{position:absolute;left:200px;top:100px;width:290px;height:360px;background:linear-gradient(160deg,#f3f1ee,#d9d3cc)}
.badge{position:absolute;left:440px;top:112px;width:96px;height:96px;border-radius:50%;background:#b51c24}
.offer-copy{position:absolute;left:620px;top:130px;width:460px}
.offer-copy h2{color:var(--blue);font-size:34px;font-weight:700}
.offer-item{display:flex;gap:12px;margin-top:24px;font-size:15px;line-height:1.45}
.offer-item b{display:block;font-size:16px}
.tick{flex:none;width:22px;height:22px;border-radius:50%;background:var(--blue);display:flex;align-items:center;justify-content:center}
.offer-copy .btn{margin-top:30px;background:var(--blue)}

/* footer */
.footer{position:absolute;top:3520px;left:0;width:1200px;height:452px;background:var(--footer);color:var(--white)}
.footer h3{font-size:22px;font-weight:600;text-transform:uppercase;padding-bottom:12px;border-bottom:1px solid #444}
.fcol{position:absolute;top:54px}
.links li{list-style:none;font-size:16px;margin-top:14px;display:flex;align-items:center;gap:10px}
.links li::before{content:"";width:7px;height:7px;background:var(--white);transform:rotate(45deg)}
.socials{display:flex;gap:8px;margin-top:18px}
.socials span{width:26px;height:26px;border-radius:50%;border:1.5px solid var(--white)}
.contact-row{display:flex;gap:14px;margin-top:22px;font-size:16px;line-height:1.5}
.cicon{flex:none;width:34px;height:34px;border-radius:50%;background:var(--blue);display:flex;align-items:center;justify-content:center}
.field{width:350px;height:38px;border:1px solid #555;background:#141416;margin-top:12px;padding:9px 12px;font-size:15px;color:#cfd3d8}
.submit{width:350px;height:40px;margin-top:12px;background:var(--blue);text-align:center;line-height:40px;font-weight:600;font-size:17px;font-family:"Poppins",sans-serif}
.divider{position:absolute;left:320px;top:54px;width:1px;height:290px;background:#333}
.divider.two{left:650px}
.copyright{position:absolute;left:0;right:0;bottom:18px;text-align:center;font-size:14px;border-top:1px solid #333;padding-top:16px;margin:0 60px}
</style>
</head>
<body>

<header class="hero">
  <svg class="hero-bg" width="1200" height="640" viewBox="0 0 1200 640" aria-hidden="true">
    <path d="M0 0H700C640 120 590 260 620 400C645 520 600 600 540 640H0Z" fill="#1f8fe6"/>
    <path d="M660 0H720C660 140 620 280 650 420C670 520 640 600 600 640H560C610 590 640 510 620 410C590 270 620 130 660 0Z" fill="#8ec8f3" opacity=".6"/>
  </svg>
  <div class="brand"><span class="brand-dot"></span>Tidewell Pillow</div>
  <span class="btn btn-blue hero-buy">Buy Now</span>
  <div class="hero-copy">
    <div class="stars">★★★★★</div>
    <div class="quote">BEST SLEEP I'VE EVER HAD" – MAYA R.</div>
    <h1>ADJUST IT.<br>FLUFF IT. LOVE IT.</h1>
    <p>Shop the adjustable Tidewell Pillow and get the best sleep of your life.</p>
    <span class="btn">Try it now &amp; get $20 off</span>
    <div class="guarantee">90-Day Money Back Guarantee</div>
  </div>
  <div class="hero-photo" role="img" aria-label="Smiling woman hugging a white Tidewell pillow inside a cloud-shaped frame"></div>
</header>

<section class="perks">
  <div class="perk" style="left:160px">
    <div class="perk-ring"><svg width="44" height="44" viewBox="0 0 24 24" fill="none" stroke="#fff" stroke-width="1.8"><path d="M2 7h11v9H2zM13 10h4l3 3v3h-7z"/><circle cx="6" cy="17" r="2" fill="#1f8fe6"/><circle cx="17" cy="17" r="2" fill="#1f8fe6"/></svg></div>
    Free Shipping</div>
  <div class="perk" style="left:480px">
    <div class="perk-ring"><svg width="44" height="44" viewBox="0 0 24 24" fill="none" stroke="#fff" stroke-width="1.8"><path d="M15 4a8 8 0 1 0 5 13A7 7 0 0 1 15 4z"/></svg></div>
    90-Night Free Trial</div>
  <div class="perk" style="left:780px">
    <div class="perk-ring"><svg width="44" height="44" viewBox="0 0 24 24" fill="none" stroke="#fff" stroke-width="1.8"><circle cx="12" cy="10" r="6"/><path d="M8 15l-2 7 6-3 6 3-2-7"/></svg></div>
    3-Years Warranty</div>
  <svg style="position:absolute;left:330px;top:150px" width="540" height="30" aria-hidden="true"><path d="M0 25Q135 -5 270 12T540 25" fill="none" stroke="#bcd8f0" stroke-width="2"/></svg>
</section>

<section class="pillows">
  <h2 class="section-title">The Perfect Pillow for a Better Night's Sleep</h2>
  <div class="arrow" style="left:20px;top:350px"><svg width="14" height="14" viewBox="0 0 14 14"><path d="M9 2L4 7l5 5" fill="none" stroke="#333" stroke-width="2"/></svg></div>
  <div class="arrow" style="left:1140px;top:350px"><svg width="14" height="14" viewBox="0 0 14 14"><path d="M5 2l5 5-5 5" fill="none" stroke="#333" stroke-width="2"/></svg></div>
  <div class="pillow-card" style="left:140px">
    <div class="pillow-img" role="img" aria-label="Stack of white adjustable pillows"></div>
    <h3>Adjustable for all sleepers.</h3>
    <p>Everyone sleeps differently, so why should you settle for a one-size-fits-all pillow? With the Tidewell Pillow you can add or remove filling to customize</p>
  </div>
  <div class="pillow-card" style="left:450px">
    <div class="pillow-img" role="img" aria-label="Stack of white adjustable pillows"></div>
    <h3>Adjustable for all sleepers.</h3>
    <p>Everyone sleeps differently, so why should you settle for a one-size-fits-all pillow? With the Tidewell Pillow you can add or remove filling to customize</p>
  </div>
  <div class="pillow-card" style="left:760px">
    <div class="pillow-img" role="img" aria-label="Stack of white adjustable pillows"></div>
    <h3>Adjustable for all sleepers.</h3>
    <p>Everyone sleeps differently, so why should you settle for a one-size-fits-all pillow? With the Tidewell Pillow you can add or remove filling to customize</p>
  </div>
</section>

<section class="positions">
  <p class="kicker">Designed for the</p>
  <h2 class="section-title">Sleep you Deserve!</h2>
  <div class="pos-card" style="left:140px;top:240px"><div class="pos-icon b"><svg width="40" height="30" viewBox="0 0 40 30" fill="#fff"><rect x="2" y="18" width="36" height="6"/><circle cx="10" cy="12" r="5"/></svg></div>Fully adjustable for all<br>sleep positions</div>
  <div class="pos-card" style="left:460px;top:240px"><div class="pos-icon o"><svg width="40" height="30" viewBox="0 0 40 30" fill="#fff"><rect x="2" y="18" width="36" height="6"/><circle cx="10" cy="12" r="5"/></svg></div>Fully adjustable for all<br>sleep positions</div>
  <div class="pos-card" style="left:780px;top:240px"><div class="pos-icon b"><svg width="40" height="30" viewBox="0 0 40 30" fill="#fff"><rect x="2" y="18" width="36" height="6"/><circle cx="10" cy="12" r="5"/></svg></div>Fully adjustable for all<br>sleep positions</div>
  <div class="pos-card" style="left:300px;top:450px"><div class="pos-icon o"><svg width="40" height="30" viewBox="0 0 40 30" fill="#fff"><rect x="2" y="18" width="36" height="6"/><circle cx="10" cy="12" r="5"/></svg></div>Fully adjustable for all<br>sleep positions</div>
  <div class="pos-card" style="left:620px;top:450px"><div class="pos-icon o"><svg width="40" height="30" viewBox="0 0 40 30" fill="#fff"><rect x="2" y="18" width="36" height="6"/><circle cx="10" cy="12" r="5"/></svg></div>Fully adjustable for all<br>sleep positions</div>
</section>

<section class="reviews">
  <h2 class="section-title">What Our Customer are Saying...</h2>
  <div class="arrow" style="left:30px;top:290px"><svg width="14" height="14" viewBox="0 0 14 14"><path d="M9 2L4 7l5 5" fill="none" stroke="#333" stroke-width="2"/></svg></div>
  <div class="arrow" style="left:1130px;top:290px"><svg width="14" height="14" viewBox="0 0 14 14"><path d="M5 2l5 5-5 5" fill="none" stroke="#333" stroke-width="2"/></svg></div>
  <div class="review" style="left:140px"><div class="stars">★★★★★</div><p>I used to wake up with a stiff neck every morning. After removing a little filling, this pillow fits me perfectly and I sleep straight through the night now. Worth every cent.</p><hr><div class="reviewer"><div class="avatar" role="img" aria-label="Customer portrait"></div><div><b>Sam Porter</b><span>Florida, United States</span></div></div></div>
  <div class="review" style="left:450px"><div class="stars">★★★★★</div><p>Soft, cool and easy to shape. I sleep on my side and finally found the right height. Shipping was quick and the fabric still feels brand new after many washes.</p><hr><div class="reviewer"><div class="avatar" role="img" aria-label="Customer portrait"></div><div><b>Sam Porter</b><span>Florida, United States</span></div></div></div>
  <div class="review" style="left:760px"><div class="stars">★★★★★</div><p>My partner and I each ordered one and tuned them to our own taste. Best purchase for our bedroom this year, and the free trial made the choice easy.</p><hr><div class="reviewer"><div class="avatar" role="img" aria-label="Customer portrait"></div><div><b>Sam Porter</b><span>Florida, United States</span></div></div></div>
</section>

<section class="offers">
  <div class="offer-back"></div>
  <div class="offer-photo" role="img" aria-label="Woman sitting on a bed holding a white pillow"></div>
  <div class="badge" role="img" aria-label="Warranty seal"></div>
  <div class="offer-copy">
    <h2>Guarantees &amp; Offers:</h2>
    <div class="offer-item"><span class="tick"><svg width="12" height="12" viewBox="0 0 12 12"><path d="M2 6l3 3 5-6" fill="none" stroke="#fff" stroke-width="2"/></svg></span><div><b>90-Night Risk-Free Trial</b>Try the Tidewell Pillow at home for 90 nights. If you're not absolutely in love, return it for a full refund.</div></div>
    <div class="offer-item"><span class="tick"><svg width="12" height="12" viewBox="0 0 12 12"><path d="M2 6l3 3 5-6" fill="none" stroke="#fff" stroke-width="2"/></svg></span><div><b>3-Year Warranty</b>Every Tidewell Pillow comes with a full 3-year warranty.</div></div>
    <span class="btn">Try it now &amp; get $20 off</span>
  </div>
</section>

<footer class="footer">
  <div class="fcol" style="left:90px;width:200px">
    <h3>Quick Links</h3>
    <ul class="links"><li>Home</li><li>About</li><li>Product</li><li>Industries We Serve</li><li>Resources</li><li>Contact</li></ul>
    <div class="socials"><span></span><span></span><span></span><span></span></div>
  </div>
  <div class="divider"></div>
  <div class="fcol" style="left:350px;width:270px">
    <h3>Contact Details</h3>
    <div class="contact-row"><span class="cicon"><svg width="16" height="16" viewBox="0 0 24 24" fill="#fff"><path d="M6 2l4 4-2 3c1 3 4 6 7 7l3-2 4 4-3 4C10 21 3 14 2 5z"/></svg></span><div><b>Phone:</b><br>+1 555 0142 880</div></div>
    <div class="contact-row"><span class="cicon"><svg width="16" height="16" viewBox="0 0 24 24" fill="none" stroke="#fff" stroke-width="2"><rect x="3" y="5" width="18" height="14"/><path d="M3 6l9 7 9-7"/></svg></span><div><b>Email:</b><br>hello@tidewellpillow.com</div></div>
    <div class="contact-row"><span class="cicon"><svg width="16" height="16" viewBox="0 0 24 24" fill="#fff"><path d="M12 2a7 7 0 0 0-7 7c0 5 7 13 7 13s7-8 7-13a7 7 0 0 0-7-7zm0 10a3 3 0 1 1 0-6 3 3 0 0 1 0 6z"/></svg></span><div><b>Address:</b><br>Tidewell Home Goods, United States</div></div>
  </div>
  <div class="divider two"></div>
  <div class="fcol" style="left:700px;width:360px">
    <h3>Contact Me</h3>
    <div class="field">Name:</div>
    <div class="field">Email:</div>
    <div class="field">Address:</div>
    <div class="submit">Submit Now</div>
  </div>
  <div class="copyright">Copyright@2025 Tidewell Home Goods. All Rights Reserved</div>
</footer>

</body>
</html>
```